Web Design Project

Psychotherapy and Counselling Practice needs a landing page web design.

My business "Larkfield Advisory" specialises in the treatment of Anxiety and Depression with a holistic approach, endeavouring to unlock the key that holds us to ransom in a life that is imbalanced, frustrating, and ultimately of our own making due to our own perceptions and behaviours.

There is much that impacts us which we cannot change, but we are always in control of how we think, and how we frame our experiences.....learning to challenge those thoughts and behaviours that are destructive and disempowering opens up a world of joyful possibility. Life is about making choices, learn to make wiser and healthier choices.......

Larkfield Advisory has a client base of individual clients but will seek to expand to offer services to the Corporate world by offering an adjunct to employers for established "Wellness Programs".

Larkfield Advisory is a highly professional, ethically bound business, with the needs of the client at the forefront of all we do.

Larkfield Advisory wishes to avoid the usual "jargon driven" psychobabble offered on many counselling web pages. It aims to be stylishly presented, clean in look and with as few "words" as possible and a largely white background (faster loading and more powerful impact of what is stated), those words contained in the webpage should be meaningful, persuasive and have an impact simply at glance. Larkfield does not want , or expect, those prospective clients in need of support , to be reading through volumes of industry driven cliches.

At this point Larkfield is just looking for a high quality landing page. However in time this will likely expand to include other sections such as case studies, video content etc.

Target Market(s)

Those in need of emotional support, suffering mental health issues, and those simply wanting to become self aware supported by a mindful therapist.

Industry/Entity Type

Industry

Requirements
Must have
• The design must incorporate the Larkfield logo and colour schemes found on the attached files.

```html
<!DOCTYPE html>
<html lang="en">
<head>
<meta charset="utf-8">
<title>Larkfield Advisory</title>
<link href="https://fonts.googleapis.com/css2?family=Open+Sans:wght@400;600;700&display=swap" rel="stylesheet">
<style>
  :root {
    --leaf: #8cad0f;
    --slate: #717171;
    --mist: #8f8f8f;
    --ink: #6a6a6a;
    --paper: #ffffff;
  }
  * { margin: 0; padding: 0; box-sizing: border-box; }
  html, body { width: 1200px; height: 1000px; overflow: hidden; background: var(--paper); }
  body { font-family: "Open Sans", Arial, sans-serif; position: relative; }

  .site-header { position: absolute; inset: 0 0 auto 0; height: 248px; background: var(--leaf); }
  .site-header .band { position: absolute; left: 0; right: 0; top: 196px; height: 52px; background: var(--slate); }

  .brand-box { position: absolute; left: 85px; top: 0; width: 300px; height: 248px; background: var(--slate); border-top: 4px solid #9a9a9a; }
  .brand-name { position: absolute; left: 0; right: 0; top: 104px; text-align: center; font-size: 34px; font-weight: 400; letter-spacing: 2px; color: var(--paper); text-transform: uppercase; }
  .brand-tagline { position: absolute; left: 14px; top: 177px; width: 271px; height: 54px; background: var(--leaf); color: var(--paper); font-size: 16px; font-weight: 700; display: flex; align-items: center; justify-content: center; }

  .main-nav { position: absolute; top: 175px; left: 635px; display: flex; }
  .main-nav a { color: var(--paper); text-decoration: none; font-size: 17px; font-weight: 700; margin-right: 30px; }
  .main-nav a.case { margin-left: 20px; margin-right: 0; }

  .hero { position: absolute; left: 0; top: 248px; width: 1200px; height: 652px; }
  .hero-mark { position: absolute; left: 80px; top: 292px; font-size: 72px; font-weight: 400; letter-spacing: 3px; color: var(--leaf); text-transform: uppercase; }
  .hero-wave { position: absolute; left: 0; top: 540px; }

  .hero-copy { position: absolute; left: 698px; top: 100px; color: var(--mist); font-weight: 700; }
  .quote { font-size: 28px; line-height: 44px; }
  .quote .second { padding-left: 16px; display: block; }
  .quote-source { font-size: 16px; margin: 8px 0 0 16px; }
  .pledge { font-size: 21px; margin: 100px 0 0 16px; }
  .pledge .accent { color: var(--leaf); }
  .therapist { margin: 40px 0 0 16px; font-size: 22px; }
  .credentials { margin: 4px 0 0 16px; font-size: 16px; }
  .contact { margin: 30px 0 0 16px; font-size: 16px; line-height: 27px; }

  .site-footer { position: absolute; left: 0; top: 900px; width: 1200px; height: 100px; }
  .copyright { position: absolute; left: 83px; top: 37px; font-size: 12px; font-weight: 700; color: var(--ink); }
  .social { position: absolute; left: 406px; top: 27px; display: flex; gap: 11px; }
  .social span { width: 30px; height: 29px; background: var(--leaf); display: block; }
  .web-address { position: absolute; right: 98px; top: 32px; font-size: 16px; font-weight: 700; color: var(--ink); }
  .web-address .accent { color: var(--leaf); }
</style>
</head>
<body>
  <header class="site-header">
    <div class="band"></div>
    <div class="brand-box">
      <div class="brand-name">Larkfield</div>
      <div class="brand-tagline">Consulting is that you may need</div>
    </div>
    <nav class="main-nav">
      <a href="#">HOME</a>
      <a href="#">ABOUT US</a>
      <a href="#">CONTACT US</a>
      <a href="#" class="case">CASE STUDIES</a>
    </nav>
  </header>

  <section class="hero">
    <div class="hero-mark">Larkfield</div>
    <svg class="hero-wave" width="1200" height="112" viewBox="0 0 1200 112" aria-hidden="true">
      <path d="M0 6 C300 40 700 20 1080 12 C700 30 300 50 0 46 Z" fill="var(--leaf)"/>
      <path d="M0 56 C350 70 800 40 1200 30 L1200 112 L0 112 Z" fill="var(--slate)"/>
    </svg>
    <div class="hero-copy">
      <p class="quote">“With the new day comes<span class="second">new strength new thoughts.”</span></p>
      <p class="quote-source">( Margaret Ellery )</p>
      <p class="pledge"><span class="accent">Consulting</span> is highly Professional</p>
      <p class="therapist">MARA HOLLIS</p>
      <p class="credentials">BA (Psych) BSc (Hons) Psych MBPS</p>
      <p class="contact">Mobile: 0412 308 517<br>E-mail: m.hollis@larkfieldmail.com</p>
    </div>
  </section>

  <footer class="site-footer">
    <p class="copyright">© Copyright Larkfield 2013 . Alright reserve</p>
    <div class="social"><span></span><span></span></div>
    <p class="web-address">www.<span class="accent">larkfieldadvisory</span>.com.au</p>
  </footer>
</body>
</html>
```